KLORA product web page

We need a new web design for our KLORA product page. You can find more information about the project on the current web site - www.klora.example

What we need from a new design (uncoded):
- landing pages + template
- all information on one page
- the design should be focused on the product - light bulb + app
- web site should be with some dynamics like a background with parallax effect in the current version
- fonts should be chosen
- a number of illustrations should be designed

Here is schema for a new design: https://files.examplehost.net/d/draw-7QpX2mLk9RtYv4Hs/edit

Here is a document with all texts for a new design: https://files.examplehost.net/d/doc-3WnZ8bJf5KcUe1Ga/edit

Illustrations to use:
v1 - https://files.examplehost.net/f/fold-A1kT9pQw2ZxR
v2 - https://files.examplehost.net/f/fold-B7mH4sLv6YcN

iOS screens: https://files.examplehost.net/f/fold-C3rJ8dKe1WuP

KLORA logo: https://files.examplehost.net/f/fold-D5nF2gTb9XoM
Updates

I forgot to add the definition text "KLORA - is.." to the document with texts. Sorry, my mistake.

Target Market(s)

25-45 year old adults who are interested in "smart" devices for their health.

Industry/Entity Type

Brintel

Colors

Designer to choose colors to be used in the design.

Requirements
Must have
• - landing pages + template
- fonts should be chosen

```html
<!DOCTYPE html>
<html lang="en">
<head>
<meta charset="utf-8">
<title>KLORA LED Bulb</title>
<link rel="stylesheet" href="https://fonts.googleapis.com/css2?family=Open+Sans:wght@300;400;600&display=swap">
<style>
:root{
  --bg-deep:#03081a;
  --bg-mid:#0b1a3c;
  --bg-band:#0d1a36;
  --header:#0d0d10;
  --footer:#000000;
  --accent:#1a9fe6;
  --accent-btn:#1590d6;
  --text:#ffffff;
  --text-soft:#c8d0dc;
  --card:#060c1e;
  --card-inner:#0f1628;
  --line:rgba(120,150,200,.22);
  --shot-top:#2e3038;
  --shot-bottom:#16171d;
}
*{box-sizing:border-box;margin:0;padding:0}
html,body{width:1200px;height:2932px;overflow:hidden}
body{
  position:relative;
  font-family:"Open Sans",Arial,sans-serif;
  color:var(--text);
  background:
    radial-gradient(ellipse 700px 500px at 600px 420px,#10285a 0%,transparent 70%),
    radial-gradient(ellipse 800px 600px at 900px 1300px,#0c2050 0%,transparent 70%),
    radial-gradient(ellipse 700px 500px at 300px 1800px,#0b1d48 0%,transparent 70%),
    linear-gradient(180deg,var(--bg-mid) 0%,var(--bg-deep) 40%,#050c24 70%,var(--bg-deep) 100%);
}
.abs{position:absolute}

/* header */
.site-header{position:absolute;left:0;top:0;width:1200px;height:85px;background:linear-gradient(180deg,#1a1a1e,var(--header))}
.header-bump{position:absolute;left:470px;top:40px;width:260px;height:80px;border-radius:0 0 130px 130px/0 0 70px 70px;background:var(--header)}
.nav-link{position:absolute;top:34px;font-size:14px;color:var(--text-soft);letter-spacing:.3px}
.brand{position:absolute;left:0;width:1200px;top:14px;text-align:center;font-size:46px;font-weight:600;color:var(--text);letter-spacing:4px;line-height:56px}

/* shared */
.section-title{position:absolute;font-weight:400;color:var(--accent);text-transform:uppercase;font-size:48px;line-height:56px;letter-spacing:.5px}
.centered{left:0;width:1200px;text-align:center}
.title-lines{position:absolute;height:1px;background:var(--line)}
.bullets{position:absolute;list-style:none}
.bullets li{position:relative;padding-left:32px;font-size:21px;line-height:43px;color:var(--text)}
.bullets li::before{content:"";position:absolute;left:6px;top:17px;width:9px;height:9px;border:1.5px solid var(--text-soft);border-radius:50%}
.btn{position:absolute;display:flex;align-items:center;justify-content:center;background:var(--accent-btn);color:var(--text);font-size:16px;border-radius:3px}
.divider{position:absolute;left:120px;width:960px;height:1px;background:linear-gradient(90deg,transparent,var(--line),transparent)}
.side-dots{position:absolute;left:1124px;width:20px}
.circle-btn{position:absolute;width:70px;height:70px;border:2px solid var(--text);border-radius:50%}
.product-shot{position:absolute;border-radius:8px;background:linear-gradient(180deg,var(--shot-top),var(--shot-bottom))}

/* cards */
.feature-card{position:absolute;top:948px;width:255px;height:415px;background:var(--card);border-radius:4px;box-shadow:0 0 20px rgba(0,0,0,.5)}
.feature-icon{position:absolute;left:16px;top:14px;width:223px;height:172px;background:var(--card-inner);border-radius:3px;display:flex;align-items:center;justify-content:center}
.feature-name{position:absolute;left:0;top:207px;width:100%;text-align:center;font-size:20px;font-weight:400;text-transform:uppercase}
.feature-text{position:absolute;left:24px;top:246px;width:207px;text-align:center;font-size:11px;line-height:17px;color:var(--text-soft)}

/* tech band */
.tech-band{position:absolute;left:0;top:2193px;width:1200px;height:358px;background:var(--bg-band)}
.spec-title{position:absolute;left:483px;top:2241px;font-size:23px;font-weight:600;color:var(--accent);text-transform:uppercase}
.spec-list{position:absolute;left:486px;top:2286px;width:470px;list-style:none}
.spec-list li{position:relative;padding-left:16px;font-size:12px;line-height:15px;color:var(--text-soft);margin-bottom:13px}
.spec-list li::before{content:"";position:absolute;left:0;top:5px;width:5px;height:5px;border:1px solid var(--text-soft);border-radius:50%}
.btn-small{font-size:11px;font-family:Georgia,serif;border-radius:2px}

/* footer */
.site-footer{position:absolute;left:0;top:2580px;width:1200px;height:352px;background:var(--footer)}
.connect-title{position:absolute;left:0;width:1200px;top:2620px;text-align:center;font-size:31px;font-weight:300;color:var(--text);text-transform:uppercase;letter-spacing:-.5px}
.social{position:absolute;top:2674px;width:36px;height:36px;border-radius:50%;background:var(--text)}
.copyright{position:absolute;left:0;width:1200px;top:2858px;text-align:center;font-size:12px;color:var(--text-soft)}
</style>
</head>
<body>

<header class="site-header">
  <div class="header-bump"></div>
  <span class="nav-link" style="left:158px">PRE-ORDER</span>
  <span class="nav-link" style="left:340px">BLOG</span>
  <div class="brand">KLORA</div>
  <span class="nav-link" style="left:764px">CONTACTS</span>
  <span class="nav-link" style="left:954px">RU</span>
</header>

<!-- hero -->
<section>
  <div class="title-lines" style="left:60px;top:257px;width:80px"></div>
  <div class="title-lines" style="left:520px;top:257px;width:180px"></div>
  <h1 class="section-title" style="left:143px;top:222px">KLORA LED Bulb</h1>
  <ul class="bullets" style="left:148px;top:305px">
    <li>Control KLORA lightbulbs with your mobile device</li>
    <li>iOS devices with Bluetooth 4 (LE)</li>
    <li>Android devices with Bluetooth 2.1 or 4</li>
    <li>5W incandescent equivalent</li>
  </ul>
  <div class="btn" style="left:148px;top:491px;width:192px;height:43px">Read More</div>
  <div class="product-shot" role="img" aria-label="Product photo: KLORA bulb glowing yellow beside a phone showing the app" style="left:772px;top:205px;width:323px;height:400px"></div>
  <div class="circle-btn" style="left:565px;top:589px">
    <svg width="66" height="66" viewBox="0 0 66 66"><path d="M21 28 L33 40 L45 28" fill="none" stroke="#fff" stroke-width="2.5"/></svg>
  </div>
  <svg class="side-dots" style="top:305px" width="20" height="136" viewBox="0 0 20 136"><line x1="10" y1="8" x2="10" y2="128" stroke="#fff" stroke-width="1.5"/><circle cx="10" cy="8" r="6" fill="#fff"/><circle cx="10" cy="38" r="6" fill="#fff"/><circle cx="10" cy="68" r="6" fill="#fff"/><circle cx="10" cy="98" r="6" fill="#fff"/><circle cx="10" cy="128" r="6" fill="#fff"/></svg>
</section>

<div class="divider" style="top:755px"></div>

<!-- what we do -->
<section>
  <div class="title-lines" style="left:330px;top:836px;width:110px"></div>
  <div class="title-lines" style="left:760px;top:836px;width:110px"></div>
  <h2 class="section-title centered" style="top:805px">What we do</h2>
  <p class="abs centered" style="top:878px;font-size:21px">Control KLORA lightbulbs with your mobile device</p>

  <article class="feature-card" style="left:199px">
    <div class="feature-icon">
      <svg width="80" height="80" viewBox="0 0 80 80" fill="#1a9fe6"><rect x="2" y="2" width="20" height="20" rx="3"/><rect x="30" y="2" width="20" height="20" rx="3"/><rect x="58" y="2" width="20" height="20" rx="3"/><rect x="2" y="30" width="20" height="20" rx="3"/><rect x="30" y="30" width="20" height="20" rx="3"/><rect x="58" y="30" width="20" height="20" rx="3"/><rect x="2" y="58" width="20" height="20" rx="3"/><rect x="30" y="58" width="20" height="20" rx="3"/><rect x="58" y="58" width="20" height="20" rx="3"/></svg>
    </div>
    <h3 class="feature-name">KLORA App</h3>
    <p class="feature-text">KLORA Application allows you to control each lightbulb at home. Manage your lighting by creating functional groups and adding/excluding lightbulbs. Correctly matched lighting will help you work more productively and relax to the outmost.</p>
  </article>

  <article class="feature-card" style="left:473px">
    <div class="feature-icon">
      <svg width="90" height="90" viewBox="0 0 90 90"><path d="M42 8 C18 8 4 26 6 46 C8 68 26 82 44 82 C54 82 54 72 48 66 C44 60 48 54 56 55 C72 57 82 48 80 32 C78 18 62 8 42 8 Z" fill="none" stroke="#1a9fe6" stroke-width="7"/><circle cx="24" cy="34" r="6" fill="#1a9fe6"/><circle cx="40" cy="22" r="6" fill="#1a9fe6"/><circle cx="22" cy="56" r="6" fill="#1a9fe6"/><path d="M84 8 L62 48" stroke="#1a9fe6" stroke-width="7" stroke-linecap="round"/></svg>
    </div>
    <h3 class="feature-name">KLORA&nbsp; Color</h3>
    <p class="feature-text">Experiment with millions of colors! Pick any color from the screen of your mobile lightbulb KLORA can transform conventional lighting into the night lights of Seattle or bring in the rich summer hues of Provence. Enliven your fantasies or raise your best memories in one click. Change the</p>
  </article>

  <article class="feature-card" style="left:749px">
    <div class="feature-icon">
      <svg width="60" height="100" viewBox="0 0 60 100" fill="none" stroke="#1a9fe6" stroke-width="7" stroke-linecap="round"><path d="M12 8 L48 14 M12 22 L48 28 M12 36 L48 42 M12 50 L48 56"/><path d="M18 62 L42 62 L42 74 L18 74 Z" fill="#1a9fe6"/><path d="M22 82 L38 82 M26 92 L34 92"/></svg>
    </div>
    <h3 class="feature-name">KLORA</h3>
    <p class="feature-text">KLORA lightbulb is a 85W incandescent equivalent that transforms your visual environment.<br>E27 socket: no need to change anything. Easy way to home automation at hand. And yes, you can still use those switches.</p>
  </article>

  <svg class="side-dots" style="top:846px" width="20" height="136" viewBox="0 0 20 136"><line x1="10" y1="8" x2="10" y2="128" stroke="#fff" stroke-width="1.5"/><circle cx="10" cy="8" r="6" fill="#fff"/><circle cx="10" cy="38" r="6" fill="#0b1a3c" stroke="#fff" stroke-width="1.5"/><circle cx="10" cy="68" r="6" fill="#fff"/><circle cx="10" cy="98" r="6" fill="#fff"/><circle cx="10" cy="128" r="6" fill="#fff"/></svg>
</section>

<div class="divider" style="top:1458px"></div>

<!-- health -->
<section>
  <div class="product-shot" role="img" aria-label="Product photo: two KLORA bulbs glowing yellow and blue" style="left:78px;top:1564px;width:411px;height:352px"></div>
  <div class="title-lines" style="left:820px;top:1626px;width:210px"></div>
  <h2 class="section-title" style="left:596px;top:1567px">KLORA Health</h2>
  <ul class="bullets" style="left:584px;top:1650px">
    <li>Control KLORA lightbulbs with your mobile device</li>
    <li>iOS devices with Bluetooth 4 (LE)</li>
    <li>Android devices with Bluetooth 2.1 or 4</li>
    <li>5W incandescent equivalent</li>
  </ul>
  <div class="btn" style="left:584px;top:1836px;width:192px;height:43px">Read More</div>
  <svg class="side-dots" style="top:1615px" width="20" height="136" viewBox="0 0 20 136"><line x1="10" y1="8" x2="10" y2="128" stroke="#fff" stroke-width="1.5"/><circle cx="10" cy="8" r="6" fill="#fff"/><circle cx="10" cy="38" r="6" fill="#fff"/><circle cx="10" cy="68" r="6" fill="#0b1a3c" stroke="#fff" stroke-width="1.5"/><circle cx="10" cy="98" r="6" fill="#fff"/><circle cx="10" cy="128" r="6" fill="#fff"/></svg>
</section>

<div class="divider" style="top:2021px"></div>

<!-- technical -->
<section>
  <div class="title-lines" style="left:300px;top:2104px;width:120px"></div>
  <div class="title-lines" style="left:810px;top:2104px;width:110px"></div>
  <h2 class="section-title centered" style="top:2075px">KLORA Tecnical</h2>
  <div class="tech-band"></div>
  <div class="product-shot" role="img" aria-label="Product photo: KLORA bulb in front of a phone showing the app" style="left:254px;top:2232px;width:186px;height:280px"></div>
  <h3 class="spec-title">KLORA Technical Specifications</h3>
  <ul class="spec-list">
    <li>KLORA lightbulb is a 85W incandescent equivalent that transforms your visual environment.</li>
    <li>E27 socket: no need to change anything. Easy way to home automation at hand. And yes, you can still use those switches.</li>
    <li>12.5W (110 - 230V,50Hz), 1000lm+: energy efficient LED lightbulb KLORA shines brighter than others and saves energy.</li>
    <li>2700-5500K: You are not limited in your choice of color temperature. Turn on warm or cold light depending on your activities.</li>
  </ul>
  <div class="btn btn-small" style="left:489px;top:2465px;width:101px;height:28px">MORE INFO</div>
  <svg class="side-dots" style="top:2308px" width="20" height="136" viewBox="0 0 20 136"><line x1="10" y1="8" x2="10" y2="128" stroke="#fff" stroke-width="1.5"/><circle cx="10" cy="8" r="6" fill="#fff"/><circle cx="10" cy="38" r="6" fill="#fff"/><circle cx="10" cy="68" r="6" fill="#fff"/><circle cx="10" cy="98" r="6" fill="#0d1a36" stroke="#fff" stroke-width="1.5"/><circle cx="10" cy="128" r="6" fill="#fff"/></svg>
</section>

<footer class="site-footer"></footer>
<h2 class="connect-title">Connect with us</h2>
<span class="social" style="left:486px" aria-label="Social network link"></span>
<span class="social" style="left:539px" aria-label="Social network link"></span>
<span class="social" style="left:592px" aria-label="Social network link"></span>
<span class="social" style="left:645px" aria-label="Social network link"></span>
<span class="social" style="left:699px" aria-label="Social network link"></span>
<div class="circle-btn" style="left:565px;top:2735px">
  <svg width="66" height="66" viewBox="0 0 66 66"><path d="M21 38 L33 26 L45 38" fill="none" stroke="#fff" stroke-width="2.5"/></svg>
</div>
<svg class="side-dots" style="top:2654px" width="20" height="136" viewBox="0 0 20 136"><line x1="10" y1="8" x2="10" y2="128" stroke="#fff" stroke-width="1.5"/><circle cx="10" cy="8" r="6" fill="#fff"/><circle cx="10" cy="38" r="6" fill="#fff"/><circle cx="10" cy="68" r="6" fill="#fff"/><circle cx="10" cy="98" r="6" fill="#fff"/><circle cx="10" cy="128" r="6" fill="#000" stroke="#fff" stroke-width="1.5"/></svg>
<p class="copyright">Lumentra Ltd. 2014 ©</p>

</body>
</html>
```